Business Card Design Project

use presentation folder design and my logo and make 4 over 4 business cards

Industry/Entity Type

Business

Requirements
Must have
• use the design from my presentation folder and put my logo on it

Name
Title
phone
fax
email

```html
<!DOCTYPE html>
<html lang="en">
<head>
<meta charset="utf-8">
<title>KindPath Counseling – Business Cards</title>
<link href="https://fonts.googleapis.com/css2?family=Quicksand:wght@400;500;600;700&display=swap" rel="stylesheet">
<style>
  :root {
    --backdrop: #e9e6e3;
    --slate: #a8a5a2;
    --slate-light: #b9b6b3;
    --peach: #e0c6b4;
    --peach-light: #f3e8df;
    --peach-mid: #ead8ca;
    --tile-tan: #d8bfae;
    --tile-grey: #c9cdd1;
    --accent: #8a4a22;
    --ink: #3b3633;
    --ink-soft: #5a534e;
  }
  * { margin: 0; padding: 0; box-sizing: border-box; }
  html, body { width: 1200px; height: 1000px; overflow: hidden; }
  body {
    background: var(--backdrop);
    font-family: "Quicksand", sans-serif;
    color: var(--ink);
    position: relative;
  }
  .card {
    position: absolute;
    left: 210px;
    width: 780px;
    height: 446px;
    overflow: hidden;
    box-shadow: 0 6px 18px rgba(0,0,0,0.18);
  }
  .card-front { top: 36px; background: linear-gradient(160deg, var(--slate-light), var(--slate)); }
  .card-back { top: 518px; background: var(--peach-light); }
  .card-shape { position: absolute; inset: 0; width: 100%; height: 100%; }

  .brand { position: absolute; display: flex; align-items: center; white-space: nowrap; }
  .brand-mark { border-radius: 50%; background: var(--ink-soft); flex: none; }
  .brand-name { font-weight: 500; color: var(--ink); line-height: 1; }

  .card-front .brand { left: 0; right: 0; top: 170px; justify-content: center; gap: 14px; }
  .card-front .brand-mark { width: 18px; height: 18px; }
  .card-front .brand-name { font-size: 38px; }

  .pattern-strip {
    position: absolute; left: 0; top: 0; width: 120px; height: 100%;
    background: linear-gradient(180deg, var(--tile-tan), var(--tile-grey) 45%, var(--tile-tan));
    opacity: 0.75;
  }
  .person { position: absolute; left: 250px; top: 120px; }
  .person-name { font-size: 36px; font-weight: 500; color: var(--ink); }
  .person-title { font-size: 17px; font-weight: 500; color: var(--ink-soft); margin-top: 2px; padding-left: 30px; }

  .contact {
    position: absolute; left: 250px; top: 282px;
    font-size: 17px; font-weight: 500; color: var(--ink-soft); line-height: 1.35;
  }
  .contact .label { color: var(--accent); font-weight: 700; }

  .card-back .brand { left: 560px; top: 290px; gap: 8px; }
  .card-back .brand-mark { width: 11px; height: 11px; }
  .card-back .brand-name { font-size: 18px; }
</style>
</head>
<body>

<section class="card card-front" aria-label="Card front">
  <svg class="card-shape" viewBox="0 0 780 446" preserveAspectRatio="none" aria-hidden="true">
    <path d="M0 446 L0 400 C220 300 520 250 780 250 L780 446 Z" fill="var(--peach)"/>
  </svg>
  <div class="brand">
    <span class="brand-mark"></span><span class="brand-name">KindPath Counseling</span>
  </div>
</section>

<section class="card card-back" aria-label="Card back">
  <svg class="card-shape" viewBox="0 0 780 446" preserveAspectRatio="none" aria-hidden="true">
    <path d="M560 0 C640 120 700 300 720 446 L780 446 L780 0 Z" fill="var(--peach-mid)"/>
  </svg>
  <div class="pattern-strip" role="img" aria-label="Decorative tile pattern in tan and grey"></div>

  <div class="person">
    <div class="person-name">Dorian Whitfield</div>
    <div class="person-title">Founder / CEO</div>
  </div>

  <div class="contact">
    <div>Corporate Office</div>
    <div>4410 Maple Crest Dr. N.W. Suite 210</div>
    <div>Marietta GA 30060</div>
    <div><span class="label">[P]</span> 404.555.0182 <span class="label">[F]</span> 678.555.0147</div>
    <div><span class="label">[E]</span> KindPathCounseling@mail.com</div>
  </div>

  <div class="brand">
    <span class="brand-mark"></span><span class="brand-name">KindPath Counseling</span>
  </div>
</section>

</body>
</html>
```